Webdesign für Reisebüro
Zielgruppe
Reisebüro - wir haben uns vor 20 Jahren auf Reisen nach Asien spezialisiert aber inzwischen ist unsere Kernkompetenz das individuelle Arrangieren von Fernreisen in alle Welt. Jedoch decken wir auch das komplette touristische Portfolio ab was natürlich auch nicht zu kurz kommen darf. Unsere Zielgruppe liegt tatsächlich zwischen 20—70
Aufgabenstellung
Wir bezeichnen uns als das besondere Reisebüro weil wir als Menschen besonders sind. Wir lieben es zu begeistern und das gelingt uns so gut dass wir seit bestimmt 15 Jahren komplett ohne Werbung auskommen und nur von Mundpropaganda leben. Das Design soll genau dieses Besondere zum Ausdruck bringen. Soll keine „klassische“ Reisebüroseite sein auf der man selbst Reisen suchen Und buchen kann.
Natürlich wird es zb eine Seite „Über uns“ und Zielgebietsinfos und noch andere Seiten geben. Primär geht es jetzt mal um das Design an sich das unser Programmierer dann sicher umsetzen kann.
Das Büro ist bisschen im Factory Style eingerichtet und wird aktuell noch mehr diesem Style angepasst.
Der Name Orbit Loft spiegelt den chilligen Lifestyle wieder den wir verkörpern.

```html
<!DOCTYPE html>
<html lang="de">
<head>
<meta charset="utf-8">
<title>Orbit Loft – Das besondere Reisebüro</title>
<link rel="stylesheet" href="https://fonts.googleapis.com/css2?family=Bebas+Neue&family=Merriweather:wght@400;700&family=Dancing+Script:wght@500&display=swap">
<style>
:root{
  --page:#ecebe8;
  --paper:#f4f3f0;
  --white:#ffffff;
  --ink:#3a3a3a;
  --muted:#8a8a8a;
  --rust:#b5552f;
  --topbar:#35474d;
  --sea-1:#0fb3c7;
  --sea-2:#2bc6cf;
  --sea-3:#0a8fa6;
  --contact:#8fa2b3;
  --footer:#2f3133;
  --footer-text:#9a9c9e;
}
*{box-sizing:border-box;margin:0;padding:0}
html,body{width:1200px;height:2400px;overflow:hidden;background:var(--page)}
body{font-family:"Merriweather",Georgia,serif;color:var(--ink)}
.page{width:1200px;height:2400px;display:flex;flex-direction:column}
.page > *{flex-shrink:0;overflow:hidden}

.topbar{height:32px;background:var(--topbar);color:#e6ecee;font-size:11px;display:flex;align-items:center;padding:0 60px}

.hero{height:500px;position:relative;background:radial-gradient(ellipse at 70% 40%,var(--sea-2),var(--sea-1) 45%,var(--sea-3));color:var(--white);text-align:center}
.nav{position:absolute;top:28px;left:0;right:0;display:flex;justify-content:center;align-items:center;gap:54px;font-family:"Bebas Neue",sans-serif;font-size:17px;letter-spacing:2px}
.brand{width:124px;height:124px;border-radius:50%;background:var(--white);color:var(--ink);display:flex;align-items:center;justify-content:center;font-family:"Bebas Neue",sans-serif;font-size:26px;letter-spacing:1px}
.hero-copy{position:absolute;top:250px;left:0;right:0}
.kicker{font-size:10px;letter-spacing:3px;text-transform:uppercase;font-weight:700}
.hero h1{font-family:"Bebas Neue",sans-serif;font-weight:400;font-size:50px;line-height:1.05;letter-spacing:2px;margin:16px 0 26px}
.btn{display:inline-block;background:var(--rust);color:var(--white);font-size:10px;letter-spacing:2px;text-transform:uppercase;padding:9px 22px;line-height:1.3}
.arrow{position:absolute;left:30px;top:240px;width:28px;height:28px;border:1px solid rgba(255,255,255,.8);border-radius:50%}
.dots{position:absolute;bottom:22px;left:0;right:0;display:flex;justify-content:center;gap:10px}
.dots span{width:7px;height:7px;border-radius:50%;background:rgba(255,255,255,.5)}
.dots span.on{background:var(--white)}
.dots.dark span{background:#cfcfcf}.dots.dark span.on{background:var(--rust)}

.welcome{height:270px;background:var(--paper);display:flex;justify-content:center;align-items:center;gap:50px}
.welcome-text{width:400px}
.eyebrow{font-size:9px;letter-spacing:2px;text-transform:uppercase;color:var(--muted);line-height:1.4}
.section-title{font-family:"Bebas Neue",sans-serif;font-weight:400;font-size:26px;letter-spacing:1px;line-height:1.05;margin:6px 0 10px}
.body{font-size:10.5px;line-height:1.7;color:#555}
.sign{font-family:"Dancing Script",cursive;font-size:20px;margin-top:10px;color:#555}
.photo{width:190px;height:150px;background:linear-gradient(135deg,#a3473a,#6b4a3a 50%,#c9b9a0);border:8px solid var(--white);box-shadow:0 3px 10px rgba(0,0,0,.18);transform:rotate(3deg)}

.destination{height:200px;display:flex;flex-direction:column;align-items:center;justify-content:center;color:var(--white);text-align:center}
.destination h2{font-family:"Bebas Neue",sans-serif;font-weight:400;font-size:30px;letter-spacing:1.5px;line-height:1.05;margin:8px 0 14px}
.thailand{background:linear-gradient(#e9a48a,#8a7d8f 45%,#2f3a4f)}
.vietnam{background:linear-gradient(#bfc6c4,#6f7f58 40%,#4f6a2e 70%,#6b5a2c)}
.china{background:linear-gradient(#1f2c44,#2c3e5c 50%,#3a3330)}

.reviews{height:220px;background:var(--paper);text-align:center;padding-top:24px}
.avatar{width:40px;height:40px;border-radius:50%;background:#d9a58c;margin:6px auto 10px}
.quote{width:560px;margin:0 auto;font-style:italic;font-size:10px;line-height:1.7;color:#666}
.reviewer{font-size:9px;font-weight:700;margin:6px 0 8px}
.reviews .dots{position:static}

.insta{height:380px;background:var(--white);text-align:center;padding-top:22px}
.grid{width:1140px;margin:10px auto 0;display:grid;grid-template-columns:repeat(6,1fr);gap:8px}
.tile{height:120px}
.more{display:inline-block;margin-top:14px;font-size:9px;letter-spacing:1.5px;text-transform:uppercase;color:var(--rust);text-decoration:underline;line-height:1.4}

.contact{height:260px;background:var(--contact);text-align:center;padding-top:20px;color:var(--white)}
.contact .section-title{color:#fff}
.contact .body{color:#eef2f5;width:480px;margin:0 auto 10px}
.field{width:360px;height:24px;margin:0 auto 5px;background:var(--white);color:#999;font-size:9px;text-align:left;padding:6px 8px;line-height:1.3}
.field.tall{height:40px}
.contact .btn{margin-top:5px}

.footer{height:138px;background:var(--footer);color:var(--footer-text);font-size:9px;line-height:1.6;padding:24px 0 0}
.cols{display:flex;justify-content:center;gap:120px}
.cols h3{color:#ddd;font-size:9px;letter-spacing:1.5px;text-transform:uppercase;margin-bottom:6px}
.copy{text-align:center;margin-top:16px;border-top:1px solid #3d4043;padding-top:8px}
</style>
</head>
<body>
<div class="page">
  <div class="topbar">Kontakt +49 (0)821 400 12 80 | info@orbitloft-reisen.de</div>

  <header class="hero" role="img" aria-label="Luftaufnahme einer türkisen Meeresbucht mit bewaldeter Insel und Sandstrand">
    <nav class="nav">
      <span>Willkommen</span><span>Über uns</span><span>Reiseziele</span>
      <div class="brand">Orbit Loft</div>
      <span>Impressum</span><span>Datenschutz</span><span>Kontakt</span>
    </nav>
    <div class="arrow"></div>
    <div class="hero-copy">
      <div class="kicker">Special Promotion</div>
      <h1>Windjammer Nova – von<br>Singapur nach Phuket!</h1>
      <span class="btn">Jetzt entdecken</span>
    </div>
    <div class="dots"><span class="on"></span><span></span><span></span></div>
  </header>

  <section class="welcome">
    <div class="welcome-text">
      <div class="eyebrow">Das besondere Reisebüro in Augsburg</div>
      <h2 class="section-title">Herzlich Willkommen im<br>Orbit Loft Augsburg</h2>
      <p class="body">Seit über 20 Jahren sind wir Ihr kompetenter Ansprechpartner für alle Fragen rund um Asien und natürlich auch den Rest der Welt. Unser Ziel: Sie lernen uns online kennen und besuchen uns dann im Orbit Loft in Augsburg. Wir freuen uns auf Ihren Besuch und planen gerne Ihre Reise.</p>
      <div class="sign">Ihr Orbit Loft Team</div>
    </div>
    <div class="photo" role="img" aria-label="Foto des Reisebüros mit Ladenfront"></div>
  </section>

  <section class="destination thailand" role="img" aria-label="Bergketten in Thailand bei Sonnenuntergang">
    <div class="eyebrow" style="color:#f3e6e0">Reiseziel Thailand</div>
    <h2>Atemberaubende<br>Landschaften in Thailand</h2>
    <span class="btn">Jetzt entdecken</span>
  </section>
  <section class="destination vietnam" role="img" aria-label="Reisterrassen und Berge in Vietnam">
    <div class="eyebrow" style="color:#f1f1ea">Reiseziel Vietnam</div>
    <h2>Unberührte Berge und<br>Strände in Vietnam</h2>
    <span class="btn">Jetzt entdecken</span>
  </section>
  <section class="destination china" role="img" aria-label="Beleuchtete Brücke und Skyline in China bei Nacht">
    <div class="eyebrow" style="color:#d6dbe4">Reiseziel China</div>
    <h2>Chinesische Tradition<br>trifft auf Moderne</h2>
    <span class="btn">Jetzt entdecken</span>
  </section>

  <section class="reviews">
    <div class="eyebrow">Einige Kundenmeinungen</div>
    <h2 class="section-title">Das sagen Kunden über uns</h2>
    <div class="avatar" role="img" aria-label="Porträt einer Kundin"></div>
    <p class="quote">„Die Beratung war persönlich und herzlich, jede Etappe unserer Reise war perfekt geplant. Wir kommen für unsere nächste Fernreise ganz sicher wieder ins Orbit Loft.“</p>
    <div class="reviewer">Lena Hofbauer – München</div>
    <div class="dots dark"><span class="on"></span><span></span><span></span></div>
  </section>

  <section class="insta">
    <div class="eyebrow">Orbit Loft bei Instagram</div>
    <h2 class="section-title">Lassen Sie sich inspirieren</h2>
    <div class="grid">
      <div class="tile" style="background:linear-gradient(#5d8a6a,#2fb2b8)" role="img" aria-label="Strandbungalows am Meer"></div>
      <div class="tile" style="background:#a07a68" role="img" aria-label="Reisemotiv in Braun"></div>
      <div class="tile" style="background:linear-gradient(#6b4e32,#9a5c3a)" role="img" aria-label="Markt mit Gewürzen"></div>
      <div class="tile" style="background:#b5552f" role="img" aria-label="Reisemotiv in Rostrot"></div>
      <div class="tile" style="background:linear-gradient(#4f7a4a,#8aa76a)" role="img" aria-label="Tropischer Garten"></div>
      <div class="tile" style="background:linear-gradient(#e07a2c,#3a6ea6)" role="img" aria-label="Orange Schirme unter blauem Himmel"></div>
      <div class="tile" style="background:linear-gradient(#6fc2e0,#2a8fb8)" role="img" aria-label="Longtailboot am Strand"></div>
      <div class="tile" style="background:#7a8a9a" role="img" aria-label="Reisemotiv in Blaugrau"></div>
      <div class="tile" style="background:linear-gradient(#7fa8c9,#c25a3a)" role="img" aria-label="Bunter Tempel"></div>
      <div class="tile" style="background:linear-gradient(#3a2a3a,#b5552f)" role="img" aria-label="Reisende bei Sonnenuntergang"></div>
      <div class="tile" style="background:linear-gradient(#3f6f8a,#2fa6b8)" role="img" aria-label="Insel im türkisen Meer"></div>
      <div class="tile" style="background:linear-gradient(#c98a5a,#5a4a3a)" role="img" aria-label="Altstadtgasse in Asien"></div>
    </div>
    <span class="more">Weitere Ansichten laden</span>
  </section>

  <section class="contact">
    <h2 class="section-title">Nehmen Sie Kontakt zu uns auf</h2>
    <p class="body">Schreiben Sie uns Ihre Reisewünsche, wir melden uns schnell bei Ihnen und planen gemeinsam Ihre ganz persönliche Fernreise.</p>
    <div class="field">Name angeben*</div>
    <div class="field">E-Mail angeben*</div>
    <div class="field tall">Nachricht*</div>
    <span class="btn">Nachricht senden</span>
  </section>

  <footer class="footer">
    <div class="cols">
      <div><h3>Kontakt</h3>Orbit Loft<br>Lindenstraße 12, 86150 Augsburg<br>Telefon: +49 (0)821 400 12 80</div>
      <div><h3>Öffnungszeiten</h3>Montag – Freitag<br>10:00 – 13:00 Uhr, 14:00 – 18:00 Uhr<br>Samstag 10:00 – 13:00 Uhr</div>
      <div><h3>Rechtliches</h3>Impressum<br>Datenschutzerklärung<br>Reisebedingungen</div>
    </div>
    <div class="copy">Copyright © 2024 Orbit Loft</div>
  </footer>
</div>
</body>
</html>
```